Quality Monitoring Company Needs a New Site

We are an established company that has a fair number of clients but the site lacks current design standards that we'd like to keep up with. We'd like to mimic the same style of the site on plinkora.com, vetrumo.com, https://brindlecoffer.com/, etc. We'd also like to make sure the designer understands SEO Silos and how it effects the design elements. Attached is the structure that I'd like to follow for the pages. You don't need to design every single sub-page because they'll probably be fairly similar; however, I want to see at least 1 each. Please use the content on our current site for filler areas. Please try to do a good job of understanding what we do so you can use your best judgement on what is needed to be successful. Use our color scheme and the logo should be the side view but I included the AI just in case.
Updates

I am narrowing down on the field of designs that I have received. There are a lot of similarities between the designs I like and don't like. I'd also like to ensure that some of the inner pages get done in the next 5 days so I can see the creativity that is there as well. That is probably what is next -- getting a few inner pages completed so I can see what you can come up with (not based on our current website) because the current "front pages" are all so good and so close.

Industry/Entity Type

Telecommunications

Colors

Designer to choose colors to be used in the design.

Requirements
Must have
• SEO Silo Look and Feel
• Current Colors
Should not have
• No stockphotos whatsoever. NONE.

```html
<!DOCTYPE html>
<html lang="en">
<head>
<meta charset="utf-8">
<title>Tellwise — Contact</title>
<link rel="stylesheet" href="https://fonts.googleapis.com/css2?family=Poppins:wght@400;500;600;700&display=swap">
<style>
:root{
  --navy:#002e57;
  --sky:#08b4e6;
  --bg:#f5f6fb;
  --bg-curve:#eceef7;
  --text:#3a3f4a;
  --muted:#9aa1ad;
  --line:#d3d7e0;
  --white:#ffffff;
}
*{box-sizing:border-box;margin:0;padding:0}
html,body{width:1190px;height:1200px;overflow:hidden}
body{position:relative;background:var(--bg);font-family:"Poppins",sans-serif;color:var(--text)}
.abs{position:absolute}
.bg-curve{left:0;top:0}
.brand{left:140px;top:70px;display:flex;align-items:center;gap:8px;font-size:21px;font-weight:500;color:var(--navy)}
.brand-dot{width:12px;height:12px;border-radius:50%;background:var(--sky)}
.nav{left:400px;top:76px;display:flex;gap:23px;font-size:12.5px;color:#333}
.nav .active{color:var(--sky);font-weight:600}
.head-phone{left:896px;top:63px;display:flex;align-items:center;gap:9px;font-size:14px;font-weight:700;color:var(--navy)}
.head-phone .disc{width:38px;height:38px;border-radius:50%;background:var(--sky);display:flex;align-items:center;justify-content:center}
.section-title{font-size:29px;font-weight:700;color:var(--navy);line-height:1}
.section-title span{color:var(--sky);font-weight:400}
.rule{width:35px;height:2px;background:var(--sky)}
.connect-title{left:143px;top:197px}
.connect-rule{left:143px;top:241px}
.tagline{left:143px;top:263px;font-size:13px;letter-spacing:.3px;color:#555}
.info{left:140px;display:flex;gap:14px}
.info svg{flex:none}
.info h4{font-size:13px;font-weight:600;color:var(--navy);line-height:19px}
.info p{font-size:13px;line-height:19px;color:#333;letter-spacing:.4px}
.card{left:594px;top:159px;width:455px;height:420px;background:var(--white);border-radius:18px;box-shadow:0 18px 40px rgba(8,180,230,.08)}
.inquiry-title{left:40px;top:38px}
.inquiry-rule{left:40px;top:82px}
.field{left:36px;width:385px;height:38px;border:1px solid var(--line);border-radius:2px;display:flex;align-items:center;gap:12px;padding-left:12px;font-size:12.5px;color:var(--muted)}
.field.message{height:95px;align-items:flex-start;padding-top:11px}
.submit{left:38px;top:350px;width:126px;height:35px;border-radius:18px;background:var(--sky);color:var(--white);font-weight:700;font-size:13px;letter-spacing:.6px;display:flex;align-items:center;justify-content:center}
.footer-band{left:0;top:829px;width:1190px;height:371px;background:var(--navy)}
.shout{left:209px;top:725px;width:770px;height:210px;border-radius:105px;background:var(--sky);text-align:center}
.shout h2{margin-top:50px;font-size:43px;font-weight:400;color:var(--white);letter-spacing:.5px}
.shout .cta{display:inline-block;margin-top:13px;width:154px;height:35px;line-height:35px;border-radius:18px;background:var(--navy);color:var(--white);font-size:13px;letter-spacing:.6px}
.foot-title{font-size:17px;font-weight:700;color:var(--sky)}
.links{font-size:11.5px;color:var(--white);line-height:20px;list-style:none}
.foot-contact{display:flex;gap:7px;font-size:12.5px;line-height:23px;color:var(--white)}
.foot-contact svg{margin-top:5px;flex:none}
.foot-brand{left:930px;top:1025px;display:flex;align-items:center;gap:10px;font-size:28px;font-weight:500;color:var(--sky)}
.foot-brand .sq{width:18px;height:18px;background:var(--white)}
.foot-rule{left:138px;top:1153px;width:911px;height:1px;background:#1e4a72}
.copyright{left:0;top:1168px;width:1190px;text-align:center;font-size:12.5px;color:var(--white)}
</style>
</head>
<body>
<svg class="abs bg-curve" width="1190" height="620" viewBox="0 0 1190 620" aria-hidden="true">
  <path d="M850 0 C780 60 700 130 690 200 C700 420 900 600 1190 590 L1190 0 Z" fill="var(--bg-curve)"/>
</svg>

<header>
  <div class="abs brand"><span class="brand-dot"></span>Tellwise</div>
  <nav class="abs nav">
    <span>Home</span><span>Services</span><span>Industries</span><span>Pricing</span><span class="active">Team</span><span>Blog</span><span>Contact Us</span>
  </nav>
  <div class="abs head-phone">
    <span class="disc"><svg width="15" height="15" viewBox="0 0 24 24"><path fill="#fff" d="M6.6 10.8a15.1 15.1 0 0 0 6.6 6.6l2.2-2.2c.3-.3.7-.4 1-.2 1.1.4 2.3.6 3.6.6.6 0 1 .4 1 1V20c0 .6-.4 1-1 1A17 17 0 0 1 3 4c0-.6.4-1 1-1h3.5c.6 0 1 .4 1 1 0 1.3.2 2.5.6 3.6.1.3 0 .7-.2 1z"/></svg></span>
    555-210-4870
  </div>
</header>

<main>
  <section class="connect">
    <h1 class="abs section-title connect-title">Connect <span>Us</span></h1>
    <div class="abs rule connect-rule"></div>
    <p class="abs tagline">Connect with us. Visit us. Work with us.</p>

    <div class="abs info" style="top:312px">
      <svg width="33" height="33" viewBox="0 0 32 32" fill="none" stroke="var(--sky)" stroke-width="1.3"><path d="M8 4l4 6-2.5 2.5a14 14 0 0 0 8 8L20 18l6 4-2 4c-9 1-20-10-19-19z"/><path d="M18 6a8 8 0 0 1 8 8M18 2a12 12 0 0 1 12 12"/></svg>
      <div><h4>Phone</h4><p>555-210-4870</p></div>
    </div>
    <div class="abs info" style="top:393px">
      <svg width="36" height="36" viewBox="0 0 36 36" fill="none" stroke="var(--sky)" stroke-width="1.3"><path d="M18 30s-9-9-9-16a9 9 0 0 1 18 0c0 7-9 16-9 16z"/><circle cx="18" cy="13" r="4"/><path d="M9 26H3l-2 6h34l-2-6h-6"/></svg>
      <div><h4>Address</h4><p>4810 Harbor Crest Ave.<br>Milvale, CA 90218</p></div>
    </div>
    <div class="abs info" style="top:494px">
      <svg width="35" height="35" viewBox="0 0 36 36" fill="none" stroke="var(--sky)" stroke-width="1.3"><path d="M2 14v19h32V14"/><path d="M2 33l13-11M34 33L21 22M2 14l16 12 16-12"/><rect x="8" y="3" width="20" height="16"/><circle cx="18" cy="10" r="3"/></svg>
      <div><h4>Email</h4><p>hello@tellwise.com</p></div>
    </div>
  </section>

  <form class="abs card">
    <h2 class="abs section-title inquiry-title">Inquiry <span>Now</span></h2>
    <div class="abs rule inquiry-rule"></div>
    <label class="abs field" style="top:100px">
      <svg width="11" height="12" viewBox="0 0 12 12"><circle cx="6" cy="3.2" r="3" fill="var(--sky)"/><path d="M0 12c0-4 2.5-5.5 6-5.5S12 8 12 12z" fill="var(--sky)"/></svg>Name</label>
    <label class="abs field" style="top:147px">
      <svg width="12" height="12" viewBox="0 0 24 24"><path fill="var(--sky)" d="M6.6 10.8a15.1 15.1 0 0 0 6.6 6.6l2.2-2.2c.3-.3.7-.4 1-.2 1.1.4 2.3.6 3.6.6.6 0 1 .4 1 1V20c0 .6-.4 1-1 1A17 17 0 0 1 3 4c0-.6.4-1 1-1h3.5c.6 0 1 .4 1 1 0 1.3.2 2.5.6 3.6.1.3 0 .7-.2 1z"/></svg>Phone</label>
    <label class="abs field" style="top:194px">
      <svg width="13" height="10" viewBox="0 0 13 10"><rect width="13" height="10" rx="1" fill="var(--sky)"/><path d="M0 1l6.5 4.5L13 1" stroke="#fff" fill="none"/></svg>Email</label>
    <label class="abs field message" style="top:241px">
      <svg width="13" height="13" viewBox="0 0 14 14" fill="none" stroke="var(--sky)" stroke-width="1.4"><path d="M7 2H1v11h11V7"/><path d="M5 9l1-3 6-5 2 2-6 5z"/></svg>Message</label>
    <div class="abs submit">SUBMIT</div>
  </form>

  <div class="abs footer-band"></div>
  <section class="abs shout">
    <h2>Give Us A Shout</h2>
    <span class="cta">GET IN TOUCH</span>
  </section>
</main>

<footer>
  <h3 class="abs foot-title" style="left:138px;top:988px">Quick Links</h3>
  <ul class="abs links" style="left:138px;top:1023px"><li>Home</li><li>Services</li><li>System Details</li><li>Pricing</li></ul>
  <ul class="abs links" style="left:291px;top:1023px"><li>Team</li><li>Blog</li><li>Contact Us</li><li>Login</li></ul>

  <h3 class="abs foot-title" style="left:456px;top:988px">Contact Us</h3>
  <div class="abs foot-contact" style="left:458px;top:1023px">
    <svg width="11" height="15" viewBox="0 0 11 15"><path d="M5.5 15S0 8.5 0 5.5a5.5 5.5 0 0 1 11 0C11 8.5 5.5 15 5.5 15z" fill="#fff"/><circle cx="5.5" cy="5.5" r="2" fill="var(--navy)"/></svg>
    <p>4810 Harbor Crest Ave.<br>Milvale, CA 90218</p>
  </div>
  <div class="abs foot-contact" style="left:654px;top:1023px">
    <svg width="14" height="14" viewBox="0 0 24 24"><path fill="#fff" d="M6.6 10.8a15.1 15.1 0 0 0 6.6 6.6l2.2-2.2c.3-.3.7-.4 1-.2 1.1.4 2.3.6 3.6.6.6 0 1 .4 1 1V20c0 .6-.4 1-1 1A17 17 0 0 1 3 4c0-.6.4-1 1-1h3.5c.6 0 1 .4 1 1 0 1.3.2 2.5.6 3.6.1.3 0 .7-.2 1z"/></svg>
    <p>555-210-4870</p>
  </div>
  <div class="abs foot-contact" style="left:654px;top:1058px">
    <svg width="14" height="11" viewBox="0 0 13 10"><rect width="13" height="10" rx="1" fill="#fff"/><path d="M0 1l6.5 4.5L13 1" stroke="var(--navy)" fill="none"/></svg>
    <p>Hello@Tellwise.com</p>
  </div>

  <div class="abs foot-brand"><span class="sq"></span>Tellwise</div>

  <div class="abs foot-rule"></div>
  <p class="abs copyright">Copyright © 2019 TELLWISE. All Rights Reserved.</p>
</footer>
</body>
</html>
```